Brevanth Capital LLC

Need Professional Business cards for New Investment Fund

Target Market(s)

High Quality investors

Industry/Entity Type

Financial

Contact Information for Business Card

Phone Number +1 555 284 6190
Name Lukas Varenko
Title Fund Manager
email lv@FundBrevanth.com
Website www.FundBrevanth.com

Colors

Designer to choose colors to be used in the design.

Requirements
Must have
• Must have our Logo and all of the above. Must be made so lettering and loge can be raised

```html
<!DOCTYPE html>
<html lang="en">
<head>
<meta charset="utf-8">
<title>Brevanth Capital LLC — Business Card</title>
<link href="https://fonts.googleapis.com/css2?family=Arimo:wght@400;500&display=swap" rel="stylesheet">
<style>
  :root {
    --backdrop: #424b41;
    --brand-green: #5dba48;
    --ink-dark: #3f4a3f;
    --paper: #ffffff;
  }
  html, body {
    margin: 0;
    padding: 0;
    width: 1200px;
    height: 900px;
    overflow: hidden;
    background: var(--backdrop);
    font-family: "Arimo", Arial, sans-serif;
  }
  .stage {
    position: relative;
    width: 1200px;
    height: 900px;
  }
  .card {
    position: absolute;
    top: 149px;
    width: 344px;
    height: 602px;
    box-sizing: border-box;
  }
  .card--front {
    left: 222px;
    background: var(--brand-green);
    display: flex;
    align-items: center;
    justify-content: center;
  }
  .card--back {
    left: 634px;
    background: var(--paper);
    text-align: center;
  }
  .brand-name {
    font-weight: 500;
    margin: 0;
    letter-spacing: 0.02em;
    white-space: nowrap;
  }
  .card--front .brand-name {
    color: var(--paper);
    font-size: 44px;
  }
  .card--back .brand-name {
    position: absolute;
    top: 163px;
    left: 0;
    right: 0;
    color: var(--brand-green);
    font-size: 34px;
  }
  .holder-name {
    position: absolute;
    top: 318px;
    left: 0;
    right: 0;
    margin: 0;
    color: var(--brand-green);
    font-size: 21px;
    font-weight: 500;
    letter-spacing: 0.03em;
  }
  .holder-title {
    position: absolute;
    top: 343px;
    left: 0;
    right: 0;
    margin: 0;
    color: var(--ink-dark);
    font-size: 15.5px;
    letter-spacing: 0.03em;
  }
  .contact-icons {
    position: absolute;
    top: 389px;
    left: 0;
    right: 0;
    display: flex;
    justify-content: center;
    gap: 8px;
  }
  .contact-icons svg { width: 23px; height: 23px; display: block; }
  .contact-list {
    position: absolute;
    top: 434px;
    left: 0;
    right: 0;
    margin: 0;
    padding: 0;
    list-style: none;
    color: var(--ink-dark);
    font-size: 17px;
    letter-spacing: 0.03em;
  }
  .contact-list li { line-height: 29px; }
</style>
</head>
<body>
<main class="stage">
  <section class="card card--front">
    <p class="brand-name">Brevanth</p>
  </section>

  <section class="card card--back">
    <p class="brand-name">Brevanth</p>
    <h1 class="holder-name">Lukas Varenko</h1>
    <p class="holder-title">Fund Manager</p>

    <div class="contact-icons">
      <svg viewBox="0 0 24 24" aria-label="Phone">
        <circle cx="12" cy="12" r="12" fill="var(--brand-green)"/>
        <path d="M8.2 6.5l2 .1 1 2.6-1.3 1.1a7 7 0 0 0 3.8 3.8l1.1-1.3 2.6 1 .1 2c-.5.9-1.5 1.3-2.4 1.2A10 10 0 0 1 7 9c-.1-.9.3-1.9 1.2-2.5z" fill="#fff"/>
      </svg>
      <svg viewBox="0 0 24 24" aria-label="Email">
        <circle cx="12" cy="12" r="12" fill="var(--brand-green)"/>
        <rect x="6.5" y="8" width="11" height="8" fill="#fff"/>
        <path d="M6.5 8l5.5 4.5L17.5 8M6.5 16l4-3.8M17.5 16l-4-3.8" fill="none" stroke="var(--brand-green)" stroke-width="1"/>
      </svg>
      <svg viewBox="0 0 24 24" aria-label="Website">
        <circle cx="12" cy="12" r="12" fill="var(--brand-green)"/>
        <g fill="none" stroke="#fff" stroke-width="1.1">
          <circle cx="12" cy="12" r="6"/>
          <ellipse cx="12" cy="12" rx="2.6" ry="6"/>
          <path d="M6 12h12M7 9h10M7 15h10"/>
        </g>
      </svg>
    </div>

    <ul class="contact-list">
      <li>+1 555 284 6190</li>
      <li>lv@FundBrevanth.com</li>
      <li>www.FundBrevanth.com</li>
    </ul>
  </section>
</main>
</body>
</html>
```